Business Card Design Project

This is the first time we use our new logo. We need a business card that we can use both on our institutional corporate relationships and also that works for our staff that deals with consumers directly.

VELUNDA is a new company dedicated to empower consumers and to provide them with the best choices for specialized health care using the latest telemedicine technology (medicine at a distance via videoconference).

We want to print this cards in high quality materials and process. We will like designs that allow us to use UV spot varnish and other techniques that will differentiate us.

We are including Two different versions of Color logos. In addition we are including white over black background logos. Those can be used replacing the black for a color.

Please note this is the first time we will be creating any corporate materials with our new logo and colors.

Target Market(s)

34+ consumers of medium high and high socioeconomic levels.

Industry/Entity Type

Health

Requirements
Must have
• Our logo on its original colors
Should not have
• Any other graphical element or design that is not our logo

```html
<!DOCTYPE html>
<html lang="en">
<head>
<meta charset="utf-8">
<title>VELUNDA Business Card</title>
<link href="https://fonts.googleapis.com/css2?family=Jost:wght@500;600&family=Arimo:wght@400;700&display=swap" rel="stylesheet">
<style>
  :root {
    --backdrop: #e9e6e1;
    --card: #ffffff;
    --navy: #1b5079;
    --teal: #17a394;
    --blue: #2a74b8;
    --sky: #5ab4e0;
    --ink: #2b2b2b;
    --rule: #cfcfcf;
  }
  * { margin: 0; padding: 0; box-sizing: border-box; }
  html, body {
    width: 1200px;
    height: 1057px;
    overflow: hidden;
    background: var(--backdrop);
  }
  .sheet {
    position: relative;
    width: 1200px;
    height: 1057px;
  }
  .card {
    position: absolute;
    left: 220px;
    width: 760px;
    height: 434px;
    background: var(--card);
    box-shadow: 0 6px 18px rgba(0,0,0,0.18);
  }
  .card--front { top: 60px; }
  .card--back { top: 563px; }

  /* Front */
  .brand {
    position: absolute;
    display: flex;
    align-items: center;
    gap: 16px;
  }
  .brand__dot {
    width: 34px;
    height: 34px;
    border-radius: 50%;
    background: var(--teal);
    flex: none;
  }
  .brand__name {
    font-family: "Jost", sans-serif;
    font-weight: 600;
    color: var(--navy);
    letter-spacing: 0.06em;
    line-height: 1;
  }
  .card--front .brand {
    left: 48px;
    top: 190px;
  }
  .card--front .brand__name { font-size: 50px; }

  .divider {
    position: absolute;
    left: 400px;
    top: 52px;
    width: 1px;
    height: 330px;
    background: var(--rule);
  }
  .contact {
    position: absolute;
    left: 440px;
    top: 78px;
    width: 300px;
  }
  .contact__name {
    font-family: "Jost", sans-serif;
    font-weight: 600;
    font-size: 30px;
    color: var(--navy);
    line-height: 1.05;
  }
  .contact__title {
    font-family: "Arimo", sans-serif;
    font-size: 20px;
    color: var(--teal);
    margin-top: 2px;
  }
  .contact__list {
    list-style: none;
    margin-top: 28px;
    margin-left: 34px;
  }
  .contact__item {
    display: flex;
    align-items: center;
    gap: 8px;
    font-family: "Arimo", sans-serif;
    font-size: 17px;
    color: var(--ink);
    line-height: 26px;
  }
  .contact__icon {
    width: 15px;
    height: 15px;
    flex: none;
    color: var(--navy);
  }
  .contact__address {
    margin-top: 22px;
    margin-left: 34px;
    font-family: "Arimo", sans-serif;
    font-size: 17px;
    line-height: 24px;
    color: var(--ink);
  }

  /* Back */
  .card--back .brand {
    left: 50%;
    top: 150px;
    transform: translateX(-50%);
  }
  .card--back .brand__name { font-size: 64px; }
  .web {
    position: absolute;
    left: 0;
    right: 0;
    top: 290px;
    text-align: center;
    font-family: "Arimo", sans-serif;
    font-size: 24px;
    letter-spacing: 0.32em;
    color: var(--ink);
  }
  .web__domain {
    font-weight: 700;
    color: var(--navy);
  }
</style>
</head>
<body>
<main class="sheet">

  <section class="card card--front" aria-label="Business card front">
    <div class="brand">
      <span class="brand__dot"></span>
      <span class="brand__name">VELUNDA</span>
    </div>

    <div class="divider"></div>

    <div class="contact">
      <h1 class="contact__name">Your Name</h1>
      <p class="contact__title">Title</p>
      <ul class="contact__list">
        <li class="contact__item">
          <svg class="contact__icon" viewBox="0 0 16 16" aria-hidden="true"><circle cx="8" cy="8" r="7" fill="none" stroke="currentColor" stroke-width="1.4"/><path d="M5.5 4.5c.6-.4 1.2 0 1.4.5l.5 1.2c.1.4-.1.7-.4.9l-.4.3c.4 1 1.1 1.7 2 2.1l.3-.4c.2-.3.6-.5.9-.4l1.2.5c.5.2.9.8.5 1.4-.6.9-1.8 1-2.8.5-1.7-.9-3-2.2-3.8-3.9-.5-1-.3-2.1.6-2.7z" fill="currentColor"/></svg>
          012-345-6789
        </li>
        <li class="contact__item">
          <svg class="contact__icon" viewBox="0 0 16 16" aria-hidden="true"><circle cx="8" cy="8" r="7" fill="none" stroke="currentColor" stroke-width="1.4"/><path d="M5.5 4.5c.6-.4 1.2 0 1.4.5l.5 1.2c.1.4-.1.7-.4.9l-.4.3c.4 1 1.1 1.7 2 2.1l.3-.4c.2-.3.6-.5.9-.4l1.2.5c.5.2.9.8.5 1.4-.6.9-1.8 1-2.8.5-1.7-.9-3-2.2-3.8-3.9-.5-1-.3-2.1.6-2.7z" fill="currentColor"/></svg>
          012-345-6789
        </li>
        <li class="contact__item">
          <svg class="contact__icon" viewBox="0 0 16 16" aria-hidden="true"><rect x="1.5" y="4" width="13" height="9" rx="1" fill="currentColor"/><path d="M2 4.5l6 4.5 6-4.5" fill="none" stroke="#fff" stroke-width="1.2"/></svg>
          name@velunda.com
        </li>
        <li class="contact__item">
          <svg class="contact__icon" viewBox="0 0 16 16" aria-hidden="true"><circle cx="8" cy="8" r="6.5" fill="none" stroke="currentColor" stroke-width="1.3"/><ellipse cx="8" cy="8" rx="3" ry="6.5" fill="none" stroke="currentColor" stroke-width="1.1"/><path d="M1.5 8h13M2.5 5h11M2.5 11h11" stroke="currentColor" stroke-width="1"/></svg>
          www.velunda.com
        </li>
      </ul>
      <p class="contact__address">Street Name, City Name<br>State, City Zip Code</p>
    </div>
  </section>

  <section class="card card--back" aria-label="Business card back">
    <div class="brand">
      <span class="brand__dot"></span>
      <span class="brand__name">VELUNDA</span>
    </div>
    <p class="web">www.<span class="web__domain">velunda</span>.com</p>
  </section>

</main>
</body>
</html>
```